TOVR Restaurant Group Take Out Bags

We need bags designed for our restaurant group.

We are an upscale Chinese food restaurant. I have uploaded a few photos that our boss liked as inspiration. I also uploaded a few of our menus so you can see the aesthetic and our logos.

The main focus is TOVR Group, but please have all 5 logos somewhere on the bag.

Red, black and gold are the ideal color focus.

Two bag sizes, but they can have the same design.
Large: 15"W, 15"H, 8"D; Small: 10"W, 12"H, 6"D

```html
<!DOCTYPE html>
<html lang="en">
<head>
<meta charset="utf-8">
<title>TOVR Group Take Out Bag</title>
<link href="https://fonts.googleapis.com/css2?family=Josefin+Sans:wght@300;400&family=Oswald:wght@500&display=swap" rel="stylesheet">
<style>
  :root {
    --backdrop: #c8c8c8;
    --bag-red: #e42a2f;
    --bag-red-light: #e94b4e;
    --bag-red-dark: #d32429;
    --cream: #f1e4ba;
    --brand-red: #e0304a;
    --label-red: #c8242c;
  }
  html, body {
    margin: 0;
    width: 1200px;
    height: 900px;
    overflow: hidden;
    background: var(--backdrop);
  }
  .bag-artwork {
    position: absolute;
    left: 220px;
    top: 100px;
    width: 760px;
    height: 700px;
  }
  .brand-name {
    font-family: "Josefin Sans", sans-serif;
    font-weight: 400;
    fill: var(--brand-red);
  }
  .brand-sub {
    font-family: "Josefin Sans", sans-serif;
    font-weight: 300;
    fill: var(--brand-red);
  }
  .venue-name {
    font-family: "Oswald", sans-serif;
    font-weight: 500;
    fill: var(--label-red);
  }
  .venue-tag {
    font-family: "Josefin Sans", sans-serif;
    font-weight: 400;
    fill: var(--label-red);
  }
</style>
</head>
<body>
<svg class="bag-artwork" viewBox="0 0 760 700" xmlns="http://www.w3.org/2000/svg">
  <defs>
    <linearGradient id="front-red" x1="0" y1="0" x2="1" y2="1">
      <stop offset="0" stop-color="var(--bag-red)"/>
      <stop offset="1" stop-color="var(--bag-red-light)"/>
    </linearGradient>
    <linearGradient id="side-red" x1="0" y1="0" x2="0" y2="1">
      <stop offset="0" stop-color="var(--bag-red-dark)"/>
      <stop offset="1" stop-color="var(--bag-red)"/>
    </linearGradient>
  </defs>

  <!-- side gusset -->
  <rect class="side-panel" x="0" y="0" width="220" height="700" fill="url(#side-red)"
        role="img" aria-label="Red side panel with a faint hand-drawn vegetable pattern"/>
  <polygon class="side-label-patch" fill="var(--cream)"
    points="0,505 60,498 70,512 150,508 135,520 220,516 220,655 170,660 150,648 90,664 40,655 0,662"/>
  <g class="venue-list" text-anchor="middle">
    <text class="venue-name" x="40" y="585" font-size="13">THE LARK</text>
    <text class="venue-tag" x="40" y="600" font-size="7">seafood lounge</text>
    <text class="venue-name" x="112" y="560" font-size="11">JADE LANTERN</text>
    <text class="venue-tag" x="112" y="574" font-size="7">tea house</text>
    <text class="venue-name" x="182" y="600" font-size="13">HARBOURMAN</text>
    <text class="venue-tag" x="182" y="615" font-size="7">oyster bar</text>
  </g>

  <!-- front face -->
  <rect class="front-panel" x="220" y="0" width="540" height="700" fill="url(#front-red)"
        role="img" aria-label="Red front panel with an orange hand-drawn vegetable and herb pattern"/>
  <polygon class="brand-patch" fill="var(--cream)"
    points="300,215 420,205 560,200 640,170 600,195 700,185 710,225 680,260 690,330 640,365 700,345 690,455 650,470 640,505 560,500 470,520 360,535 310,505 320,470 300,400 330,340 300,290 320,250"/>
  <g class="brand-lockup" text-anchor="middle">
    <text class="brand-name" x="500" y="440" font-size="76" letter-spacing="8">TOVR</text>
    <text class="brand-sub" x="504" y="468" font-size="14" letter-spacing="14">GROUP</text>
  </g>
</svg>
</body>
</html>
```